We are a recruitment company based in Norwich/Cambridge England.
I have included our company logo which we want to remain the same.

What we are looking for is a new creative Business card which will really stand out!!

Contact Information for Business Card

Harriet Dunmore
email: Harriet@plavex.co.uk
Address: Brackwell House
Fenmoor Enterprise Park
Partridge Way
Norwich
QB9 3KX
Tel:01632 960418

```html
<!DOCTYPE html>
<html lang="en">
<head>
<meta charset="utf-8">
<title>Plavex Business Card</title>
<link href="https://fonts.googleapis.com/css2?family=Lato:wght@400;700&display=swap" rel="stylesheet">
<style>
  :root {
    --page-bg: #e9e7e4;
    --green-dark: #3f8f14;
    --green-mid: #58ad22;
    --green-light: #7cc63e;
    --frost-light: #eef0ef;
    --frost-mid: #d6dad9;
    --arc-grey: #5d5f63;
    --ink-dark: #3c3d40;
    --ink-light: #ffffff;
    --brand-green: #4f9e1f;
  }
  * { margin: 0; padding: 0; box-sizing: border-box; }
  html, body { width: 1200px; height: 969px; overflow: hidden; }
  body {
    background: var(--page-bg);
    font-family: "Lato", Arial, sans-serif;
    position: relative;
  }
  .business-card {
    position: absolute;
    left: 80px;
    top: 190px;
    width: 1040px;
    height: 590px;
    overflow: hidden;
    box-shadow: 0 14px 40px rgba(0,0,0,0.18);
  }
  .card-background { position: absolute; inset: 0; width: 100%; height: 100%; }
  .contact-block {
    position: absolute;
    left: 45px;
    top: 128px;
    color: var(--ink-light);
  }
  .holder-name { font-size: 31px; font-weight: 400; letter-spacing: 0.5px; line-height: 1.2; }
  .holder-role { font-size: 25px; font-weight: 400; letter-spacing: 0.5px; line-height: 1.3; }
  .address { margin-top: 26px; font-size: 24px; line-height: 1.35; }
  .contact-list { list-style: none; margin-top: 22px; }
  .contact-list li {
    display: flex;
    align-items: center;
    gap: 16px;
    font-size: 24px;
    line-height: 33px;
  }
  .contact-icon { width: 20px; height: 20px; fill: var(--ink-light); flex: none; }
  .brand-lockup {
    position: absolute;
    left: 668px;
    top: 232px;
    display: flex;
    flex-direction: column;
    align-items: flex-start;
  }
  .brand-row { display: flex; align-items: center; gap: 18px; }
  .brand-dot { width: 62px; height: 62px; border-radius: 50%; background: var(--brand-green); }
  .brand-name { font-size: 62px; font-weight: 700; color: var(--ink-dark); line-height: 1; }
  .brand-tagline {
    margin-top: 8px;
    margin-left: 80px;
    font-size: 15px;
    font-weight: 700;
    letter-spacing: 3px;
    color: var(--ink-dark);
  }
</style>
</head>
<body>
  <div class="business-card">
    <svg class="card-background" viewBox="0 0 1040 590" preserveAspectRatio="none" aria-hidden="true">
      <defs>
        <linearGradient id="greenPanel" x1="0" y1="0" x2="1" y2="1">
          <stop offset="0" stop-color="var(--green-mid)"/>
          <stop offset="0.45" stop-color="var(--green-light)"/>
          <stop offset="1" stop-color="var(--green-dark)"/>
        </linearGradient>
        <linearGradient id="frostPanel" x1="0" y1="0" x2="1" y2="1">
          <stop offset="0" stop-color="var(--frost-light)"/>
          <stop offset="1" stop-color="var(--frost-mid)"/>
        </linearGradient>
      </defs>
      <rect class="frost-panel" width="1040" height="590" fill="url(#frostPanel)"/>
      <path class="green-panel" d="M0 0 H860 C640 40 455 190 420 360 C405 450 425 535 450 590 H0 Z" fill="url(#greenPanel)"/>
      <path class="divider-arc" d="M870 0 C650 45 468 195 434 362 C420 450 440 535 466 590" fill="none" stroke="var(--arc-grey)" stroke-width="12"/>
    </svg>

    <div class="contact-block">
      <h1 class="holder-name">HARRIET DUNMORE</h1>
      <p class="holder-role">CEO/FOUNDER</p>
      <p class="address">Brackwell House<br>Partridge Way, QB9 3KX</p>
      <ul class="contact-list">
        <li>
          <svg class="contact-icon" viewBox="0 0 20 20" aria-hidden="true"><path d="M4 1.5l3 .5 1.5 4-2 1.5c1 2.3 2.7 4 5 5l1.5-2 4 1.5.5 3c0 1-1 2.5-2.5 2.5C7.5 17.5 2.5 12.5 2 4c0-1.5 1-2.5 2-2.5z"/></svg>
          <span>01632 960418</span>
        </li>
        <li>
          <svg class="contact-icon" viewBox="0 0 20 20" aria-hidden="true"><path d="M6 0h8a1.5 1.5 0 0 1 1.5 1.5v17A1.5 1.5 0 0 1 14 20H6a1.5 1.5 0 0 1-1.5-1.5v-17A1.5 1.5 0 0 1 6 0zm0 2.5v13h8v-13zm4 14.2a1 1 0 1 0 0 2 1 1 0 0 0 0-2z"/></svg>
          <span>01632 960527</span>
        </li>
        <li>
          <svg class="contact-icon" viewBox="0 0 20 20" aria-hidden="true"><path d="M5 1h8l2 2v4H5zM2 8h16a2 2 0 0 1 2 2v6h-3v3H3v-3H0v-6a2 2 0 0 1 2-2zm3 6v3h10v-3z"/></svg>
          <span>01632 960733</span>
        </li>
        <li>
          <svg class="contact-icon" viewBox="0 0 20 20" aria-hidden="true"><path d="M1 4h18v1.2l-9 6-9-6zm0 3.4l9 6 9-6V16H1z"/></svg>
          <span>harriet@plavex.co.uk</span>
        </li>
        <li>
          <svg class="contact-icon" viewBox="0 0 20 20" aria-hidden="true"><path d="M10 1a9 9 0 1 0 0 18 9 9 0 0 0 0-18zm-1 3l2 1-1 2 2 1v2l-2 1-2-2-2 1V8zm4 8l2-1 1.5 1.5A6.8 6.8 0 0 1 12 17z"/></svg>
          <span>www.plavex.co.uk</span>
        </li>
      </ul>
    </div>

    <div class="brand-lockup">
      <div class="brand-row">
        <span class="brand-dot"></span>
        <span class="brand-name">Plavex</span>
      </div>
      <span class="brand-tagline">Technology Recruitment</span>
    </div>
  </div>
</body>
</html>
```